Bramblewick Forage Business Cards

I need a business card with my logo, number, Facebook account, and some information about what I am selling. Green card with logo on the front. 555-214-8392 phone number, @bramblewickforage Facebook, •Orchardgrass Hay •Alfalfa Hay •Mixed Grass Hay , and “Premium Quality Hay” all written on the back.

Target Market(s)

Hay

Contact Information for Business Card

Phone number, Facebook, different types of hay.

Colors
00AB8E
00BBA5
67D7C9
C6EFE9
E9F9F6

```html
<!DOCTYPE html>
<html lang="en">
<head>
<meta charset="utf-8">
<title>Bramblewick Forage Business Cards</title>
<link href="https://fonts.googleapis.com/css2?family=Yellowtail&family=Arimo:wght@400&display=swap" rel="stylesheet">
<style>
  :root {
    --backdrop: #0f0f10;
    --card: #2a2b2d;
    --card-edge: #00a651;
    --brand-green: #00a651;
    --text-light: #ffffff;
    --rule: #6a6b6e;
    --mark-faint: #3d3e41;
  }
  * { box-sizing: border-box; margin: 0; padding: 0; }
  html, body {
    width: 1200px; height: 820px; overflow: hidden;
    background: var(--backdrop);
  }
  .canvas {
    position: relative; width: 1200px; height: 820px;
    background: radial-gradient(ellipse at 50% 40%, #1e1e20 0%, var(--backdrop) 70%);
  }
  .card {
    position: absolute; top: 262px;
    width: 520px; height: 297px;
    background: var(--card);
    border-left: 3px solid var(--card-edge);
    border-bottom: 3px solid var(--card-edge);
    overflow: hidden;
    font-family: "Arimo", Arial, sans-serif;
    color: var(--text-light);
  }
  .card--back { left: 50px; }
  .card--front { left: 630px; }

  /* Back side */
  .brand-lockup {
    position: absolute; left: 70px; top: 48px;
    display: flex; align-items: center;
  }
  .brand-dot {
    width: 58px; height: 58px; border-radius: 50%;
    background: var(--brand-green);
    flex-shrink: 0;
  }
  .brand-divider {
    width: 1px; height: 70px; background: var(--rule);
    margin: 0 16px 0 26px;
    flex-shrink: 0;
  }
  .brand-name {
    font-family: "Yellowtail", cursive;
    font-size: 30px; line-height: 1; color: var(--text-light);
    white-space: nowrap;
  }
  .section-rule {
    position: absolute; left: 44px; right: 30px; top: 152px;
    height: 1px; background: var(--rule);
  }
  .product-list {
    position: absolute; right: 22px; top: 164px;
    list-style: none; text-align: right;
    font-size: 13px; line-height: 19px;
  }
  .product-list li::after {
    content: ""; display: inline-block;
    width: 7px; height: 7px; border-radius: 50%;
    background: var(--brand-green);
    margin-left: 8px; vertical-align: 2px;
  }
  .contact-list {
    position: absolute; left: 44px; bottom: 26px;
    list-style: none; font-size: 15px;
  }
  .contact-list li {
    display: flex; align-items: center; gap: 10px; margin-top: 8px;
  }
  .contact-icon {
    width: 26px; height: 26px; border-radius: 50%;
    background: var(--brand-green);
    display: flex; align-items: center; justify-content: center;
    flex-shrink: 0;
  }

  /* Front side */
  .front-circle {
    position: absolute; left: 40px; top: 36px;
    width: 150px; height: 150px; border-radius: 50%;
    background: var(--mark-faint);
  }
  .front-name {
    position: absolute; right: 30px; top: 168px;
    font-family: "Yellowtail", cursive;
    font-size: 32px; line-height: 1; color: var(--text-light);
    white-space: nowrap;
  }
</style>
</head>
<body>
<main class="canvas">

  <section class="card card--back" aria-label="Card back">
    <div class="brand-lockup">
      <span class="brand-dot"></span>
      <span class="brand-divider"></span>
      <span class="brand-name">Bramblewick Forage</span>
    </div>

    <div class="section-rule"></div>

    <ul class="product-list">
      <li>Orchardgrass Hay</li>
      <li>Alfalfa Hay</li>
      <li>Mixed Grass Hay</li>
      <li>Premium Quality Hay</li>
    </ul>

    <ul class="contact-list">
      <li>
        <span class="contact-icon">
          <svg width="14" height="14" viewBox="0 0 24 24" aria-hidden="true">
            <path d="M6.6 10.8a15.1 15.1 0 0 0 6.6 6.6l2.2-2.2a1 1 0 0 1 1-.25 11.4 11.4 0 0 0 3.6.57 1 1 0 0 1 1 1V20a1 1 0 0 1-1 1A17 17 0 0 1 3 4a1 1 0 0 1 1-1h3.5a1 1 0 0 1 1 1c0 1.25.2 2.45.57 3.57a1 1 0 0 1-.25 1z" fill="#2a2b2d"/>
          </svg>
        </span>
        <span>555-214-8392</span>
      </li>
      <li>
        <span class="contact-icon"></span>
        <span>@bramblewickforage</span>
      </li>
    </ul>
  </section>

  <section class="card card--front" aria-label="Card front">
    <span class="front-circle"></span>
    <span class="front-name">Bramblewick Forage</span>
  </section>

</main>
</body>
</html>
```